Create a cover for English Grammar Workbook

This book describes a system to learn English in a proper way - we call it The ''Lantern Row'' System.

It focuses on not only teaching grammar and its structures, but also giving students tips on how to use it and the best ways to remember what they learn.

The cover should have 3 realistic pillars (3D), with one closer to the front to show that this book is the 1st (front) Pillar.

The title is: "Building Sentences That Stick: *A Friendly Path Through Usage"*

Author's name: Doreen Calloway

```html
<!DOCTYPE html>
<html lang="en">
<head>
<meta charset="utf-8">
<title>Building Sentences That Stick — Book Cover</title>
<link rel="stylesheet" href="https://fonts.googleapis.com/css2?family=Allura&family=Roboto+Condensed:wght@700&family=Libre+Baskerville&family=Montserrat:wght@700&display=swap">
<style>
  :root {
    --backdrop: #e3e3e3;
    --cover: #383838;
    --gold-light: #fbe98a;
    --gold-mid: #e1b93a;
    --gold-deep: #b8891c;
    --ivory: #f4f1e6;
    --frame: #e9e4d2;
    --stone-light: #f2f2f0;
    --stone-mid: #d3d3cf;
    --stone-dark: #a9a9a4;
    --ink: #2a2a2a;
  }
  * { margin: 0; padding: 0; box-sizing: border-box; }
  html, body {
    width: 1200px;
    height: 843px;
    overflow: hidden;
    background: var(--backdrop);
  }
  .stage {
    position: relative;
    width: 1200px;
    height: 843px;
  }
  .book-cover {
    position: absolute;
    left: 352px;
    top: 68px;
    width: 496px;
    height: 707px;
    background: var(--cover);
    overflow: hidden;
  }
  .title-script {
    position: absolute;
    top: 42px;
    left: 0;
    width: 100%;
    text-align: center;
    font-family: "Allura", cursive;
    font-size: 58px;
    line-height: 1;
    color: var(--ivory);
  }
  .title-main {
    position: absolute;
    left: 0;
    width: 100%;
    text-align: center;
    font-family: "Roboto Condensed", "Arial Narrow", sans-serif;
    font-weight: 700;
    font-size: 76px;
    line-height: 1;
    letter-spacing: 4px;
    text-transform: uppercase;
    background: linear-gradient(180deg, var(--gold-light) 0%, var(--gold-mid) 55%, var(--gold-deep) 100%);
    -webkit-background-clip: text;
    background-clip: text;
    color: transparent;
  }
  .title-main.line-one { top: 112px; }
  .title-main.line-two { top: 188px; }
  .subtitle {
    position: absolute;
    top: 268px;
    left: 58px;
    width: 380px;
    height: 38px;
    border: 1.5px solid var(--frame);
    display: flex;
    align-items: center;
    justify-content: center;
    font-family: "Libre Baskerville", Georgia, serif;
    font-size: 17px;
    letter-spacing: 1px;
    color: var(--gold-light);
  }
  .pillars {
    position: absolute;
    left: 0;
    top: 300px;
    width: 496px;
    height: 352px;
  }
  .author-band {
    position: absolute;
    left: 0;
    bottom: 0;
    width: 100%;
    height: 54px;
    background: linear-gradient(180deg, var(--gold-light) 0%, var(--gold-mid) 50%, var(--gold-deep) 100%);
    display: flex;
    align-items: center;
    justify-content: center;
  }
  .author-name {
    font-family: "Montserrat", Arial, sans-serif;
    font-weight: 700;
    font-size: 22px;
    letter-spacing: 5px;
    text-transform: uppercase;
    color: var(--ink);
  }
</style>
</head>
<body>
<main class="stage">
  <section class="book-cover">
    <p class="title-script">Building</p>
    <h1>
      <span class="title-main line-one">Sentences</span>
      <span class="title-main line-two">That Stick</span>
    </h1>
    <p class="subtitle">A Friendly Path Through Usage</p>

    <svg class="pillars" viewBox="0 0 496 352" role="img" aria-label="Three realistic white Ionic marble columns of differing heights, the tallest in the centre">
      <defs>
        <linearGradient id="stone" x1="0" x2="1" y1="0" y2="0">
          <stop offset="0" stop-color="var(--stone-dark)"/>
          <stop offset="0.45" stop-color="var(--stone-light)"/>
          <stop offset="1" stop-color="var(--stone-mid)"/>
        </linearGradient>
      </defs>
      <rect x="36" y="109" width="107" height="240" fill="url(#stone)"/>
      <rect x="172" y="7" width="153" height="342" fill="url(#stone)"/>
      <rect x="339" y="79" width="122" height="270" fill="url(#stone)"/>
    </svg>

    <footer class="author-band">
      <span class="author-name">Doreen Calloway</span>
    </footer>
  </section>
</main>
</body>
</html>
```